Speisekarten-Design für Tennis- und Freizeitanlage mit Restaurant und Biergarten
Zielgruppe
Tennis- und Freizeitanlage mit Restaurant und Biergarten. Zielgruppe von Jung bis Alt
Aufgabenstellung
Speise- und Getränkekarte. Klassisch und klar strukturiert. Möglichst zum selbst ausdrucken (kein Randloses Design) Möglichkeit zum selbstständigen ändern als Word Dokument. A4 Format. Hülle der Speisekarte bereits vorhanden. Siehe Fotos
Wenn möglich farbiges Logo verwenden. Alternativ habe ich noch eine schwarz weiß Variante hinzugefügt.

```html
<!DOCTYPE html>
<html lang="de">
<head>
<meta charset="utf-8">
<title>Tennis Club Restaurant – Speisekarte</title>
<link rel="stylesheet" href="https://fonts.googleapis.com/css2?family=Archivo+Narrow:wght@400;500;600&family=Roboto+Condensed:wght@400;500&display=swap">
<style>
  :root {
    --backdrop: #c8d1c7;
    --frame: #5b7a5a;
    --paper: #ece7dc;
    --ink: #2c302d;
    --ink-soft: #4a4e4a;
    --accent: #46664a;
    --rule: #6b6f6a;
    --emblem-a: #e4ddcf;
    --emblem-b: #cdbfa9;
  }
  * { box-sizing: border-box; margin: 0; padding: 0; }
  html, body { width: 1200px; height: 900px; overflow: hidden; }
  body {
    background: var(--backdrop);
    position: relative;
    font-family: "Roboto Condensed", "Arial Narrow", sans-serif;
    color: var(--ink);
  }
  .menu {
    position: absolute;
    left: 78px; top: 54px;
    width: 1045px; height: 792px;
    background: var(--frame);
    box-shadow: 0 4px 14px rgba(0,0,0,.18);
  }
  .photo { position: absolute; }
  .photo--terrace   { left: 11px;  top: 13px;  width: 236px; height: 256px; background: linear-gradient(160deg,#7fa38a 0%,#3e5a3a 45%,#8a6a48 100%); }
  .photo--guest     { left: 11px;  top: 277px; width: 236px; height: 240px; background: linear-gradient(160deg,#4f6b3c 0%,#9d8d78 50%,#8a6444 100%); }
  .photo--garden    { left: 11px;  top: 525px; width: 236px; height: 254px; background: linear-gradient(180deg,#b9cde0 0%,#6f8f77 45%,#8b6a4a 100%); }
  .photo--beer      { left: 795px; top: 13px;  width: 237px; height: 256px; background: linear-gradient(160deg,#a5bfd2 0%,#3f5f45 45%,#7d8fa8 100%); }
  .photo--diner     { left: 795px; top: 277px; width: 237px; height: 240px; background: linear-gradient(160deg,#9ab0a0 0%,#7f9c86 50%,#9a7a55 100%); }
  .photo--players   { left: 795px; top: 525px; width: 237px; height: 254px; background: linear-gradient(180deg,#3e5a44 0%,#56725a 50%,#c7c7c2 100%); }
  .page {
    position: absolute; top: 13px; height: 766px;
    background: var(--paper);
    overflow: hidden;
  }
  .page--food   { left: 247px; width: 274px; padding: 66px 18px 0 37px; }
  .page--drinks { left: 521px; width: 274px; padding: 0 20px 0 37px; border-left: 1px solid #d8d2c4; }
  .menu-title {
    font-family: "Archivo Narrow", sans-serif;
    font-weight: 500; font-size: 21px; line-height: 1.2;
    letter-spacing: .4px; margin-bottom: 18px;
  }
  .item { margin-bottom: 11px; }
  .item-head {
    display: flex; justify-content: space-between;
    font-family: "Archivo Narrow", sans-serif;
    font-weight: 500; font-size: 10px; letter-spacing: .5px;
    text-transform: uppercase;
  }
  .item-desc { font-size: 7.5px; line-height: 1.35; color: var(--ink-soft); }
  .item-desc .price { float: right; font-size: 8px; }
  .drinks-table { margin-top: 30px; }
  .drinks-table h3 {
    font-family: "Archivo Narrow", sans-serif; font-weight: 500;
    font-size: 9.5px; letter-spacing: .6px; margin-bottom: 8px;
  }
  .drinks-row {
    display: flex; justify-content: space-between;
    border-top: 1px solid var(--rule);
    padding: 5px 0 9px; font-size: 8.5px;
  }
  .drinks-row:last-child { border-bottom: 1px solid var(--rule); }
  .notice { margin-top: 26px; font-size: 8.5px; line-height: 1.35; letter-spacing: .4px; }
  .notice strong { font-weight: 500; display: block; margin-bottom: 3px; }
  .emblem {
    display: block; margin: 30px 0 0 62px;
    width: 126px; height: 92px;
    background: linear-gradient(135deg, var(--emblem-a) 0%, var(--emblem-b) 100%);
  }
  .garden-title {
    font-family: "Archivo Narrow", sans-serif; font-weight: 600;
    font-size: 19px; letter-spacing: 1px; color: var(--accent);
    margin: 24px 0 18px 9px;
  }
  .section-label { margin: 4px 0 12px; }
  .thirst { margin-top: 24px; }
  .thirst h3 {
    font-family: "Archivo Narrow", sans-serif; font-weight: 500;
    font-size: 9px; letter-spacing: .6px; text-align: center; margin-bottom: 12px;
  }
  .thirst-row {
    display: grid; grid-template-columns: 52px 1fr 30px;
    font-size: 7.5px; line-height: 1.6; color: var(--ink-soft);
  }
  .thirst-row span:last-child { text-align: right; }
</style>
</head>
<body>
  <main class="menu">
    <div class="photo photo--terrace" role="img" aria-label="Terrasse mit Holzmöbeln und grünem Sonnenschirm"></div>
    <div class="photo photo--guest" role="img" aria-label="Gast mit Sonnenhut beim Essen am Holztisch, Tennisball daneben"></div>
    <div class="photo photo--garden" role="img" aria-label="Gäste unter einem grünen Sonnenschirm im Garten"></div>

    <section class="page page--food">
      <h1 class="menu-title">TENNIS CLUB<br>RESTAURANT</h1>

      <div class="item"><div class="item-head"><span>Salat der Saison</span><span>8,90</span></div>
        <p class="item-desc">Blattsalate, Kräuter und Hausdressing<br>mit geröstetem Brot</p></div>
      <div class="item"><div class="item-head"><span>Griechischer Salat</span><span>9,50</span></div>
        <p class="item-desc">Feta, Oliven, Gurke</p></div>
      <div class="item"><div class="item-head"><span>Tomatensuppe</span><span>5,90</span></div>
        <p class="item-desc">Mit Basilikum und Sahne</p></div>
      <div class="item"><div class="item-head"><span>Flammkuchen</span><span>9,90</span></div>
        <p class="item-desc">Speck, Zwiebeln, Crème fraîche<br>frisch aus dem Ofen</p></div>
      <div class="item"><div class="item-head"><span>Ofenkartoffel</span><span>8,50</span></div>
        <p class="item-desc">Mit Kräuterquark und Salat<br>dazu Schnittlauch</p></div>
      <div class="item"><div class="item-head"><span>Club Burger</span><span>13,50</span></div>
        <p class="item-desc">Rindfleisch, Cheddar, Tomate, Zwiebeln<br>Pommes frites und Salat<br>Wahlweise auch vegetarisch</p></div>
      <div class="item"><div class="item-head"><span>Tennis Teller</span><span></span></div>
        <p class="item-desc">Kleiner Snack</p></div>
      <div class="item"><div class="item-head"><span>Beilagen</span><span>4,10</span></div>
        <p class="item-desc">Pommes, Salat oder Bratkartoffeln wählbar.<br>Hausgemachte Saucen <span class="price">4,50</span><br>Ketchup, Mayo oder Aioli<br>Wir beraten Sie gern</p></div>

      <div class="drinks-table">
        <h3>GETRÄNKE</h3>
        <div class="drinks-row"><span>Cola 0,3l</span><span>3,40</span></div>
        <div class="drinks-row"><span>Apfelschorle</span><span>3,20</span></div>
        <div class="drinks-row"><span>Mineralwasser</span><span>2,90</span></div>
        <div class="drinks-row"><span>Limonade</span><span>3,50</span></div>
      </div>

      <p class="notice"><strong>HINWEIS</strong>ALLE PREISE IN EURO INKL. MWST.<br>GUTEN APPETIT AM PLATZ</p>
    </section>

    <section class="page page--drinks">
      <div class="emblem" role="img" aria-label="Illustration mit Tennisball und Tennisschläger"></div>
      <h2 class="garden-title">MEER GARDEN</h2>

      <div class="item"><div class="item-head"><span>Bier vom Fass</span><span>4,50</span></div>
        <p class="item-desc">Helles Lagerbier aus der Region <span class="price">0,5l</span><br>Frisch gezapft im Krug<br>Dazu Brezel nach Wahl.</p></div>
      <div class="item"><div class="item-head"><span>Radler und Weizen</span><span>4,20</span></div>
        <p class="item-desc">Radler, Weizen oder alkoholfrei</p></div>
      <div class="item"><div class="item-head"><span>Weinschorle</span><span>3,90</span></div>
        <p class="item-desc">Weiß oder rot mit Wasser<br>Auch als Glas Wein<br>Gut gekühlt</p></div>
      <div class="item-head section-label"><span>Zu zwei</span></div>
      <div class="item"><div class="item-head"><span>Brotzeitplatte</span><span>12,50</span></div>
        <p class="item-desc">Wurst, Käse und Gurken <span class="price">8,90</span><br>Obatzda mit Brezel<br>Zum Teilen für zwei Personen.</p></div>
      <div class="item"><div class="item-head"><span>Brezel</span><span>3,20</span></div>
        <p class="item-desc">Frisch gebacken, mit Butter oder Obatzda<br>Dazu Radieschen und Senf</p></div>
      <div class="item"><div class="item-head"><span>Currywurst</span><span>7,90</span></div>
        <p class="item-desc">Mit Pommes frites <span class="price">8,50</span><br>Hausgemachte Currysauce<br>Scharf oder mild, mit Brot</p></div>
      <div class="item"><div class="item-head"><span>Kinder und Spieler erhalten</span><span></span></div>
        <p class="item-desc">Kleine Portionen auf Anfrage gern<br>Bei der Bedienung</p></div>

      <div class="thirst">
        <h3>• FÜR DEN DURST</h3>
        <div class="thirst-row"><span>Kaffee</span><span>Crema oder Espresso</span><span>2,80</span></div>
        <div class="thirst-row"><span>Tee</span><span>Verschiedene Sorten</span><span>2,50</span></div>
        <div class="thirst-row"><span>Kakao</span><span>Heiß oder kalt</span><span>3,00</span></div>
        <div class="thirst-row"><span>Eistee</span><span>Hausgemacht mit Zitrone</span><span>3,20</span></div>
      </div>
    </section>

    <div class="photo photo--beer" role="img" aria-label="Gast mit Bierglas an einem Tisch im Biergarten"></div>
    <div class="photo photo--diner" role="img" aria-label="Gast beim Essen mit Salatteller und Bier"></div>
    <div class="photo photo--players" role="img" aria-label="Zwei Tennisspieler stehen vor der Anlage"></div>
  </main>
</body>
</html>
```